Brochure/Catalog for Door Manufacturer and Designer

Harlow Door Design is a door manufacturer and distributor based out of the Southwest United States. We need a catalog showcasing our four door collections.
We have a clear vision on what the catalog will look like (SEE INSTRUCTIONS ATTACHED), but we need a creative designer to put it all together.
We have attached:
- Catalog instructions (brochure.doc)
- Our logo (GHN094.png)
- A zip folder with Images (images.zip)
Please read the attached brochure instructions and contact us with any questions.
Thank you for your time and we look forward to seeing your design!
Harlow Door Design
Distributor

```html
<!DOCTYPE html>
<html lang="en">
<head>
<meta charset="utf-8">
<title>Harlow Door Design — Catalog Opening Page</title>
<link rel="stylesheet" href="https://fonts.googleapis.com/css2?family=Pinyon+Script&family=Cormorant+Garamond:ital,wght@1,500&family=IM+Fell+English&family=Alice&family=Cabin:wght@400;500&display=swap">
<style>
  :root {
    --paper: #d3c1b8;
    --navy: #13285a;
    --rule: #a7775a;
    --ink: #1a1a1a;
    --ink-soft: #3d3a38;
  }
  * { margin: 0; padding: 0; box-sizing: border-box; }
  html, body { width: 1200px; height: 756px; overflow: hidden; }
  body { background: var(--paper); }
  .page {
    position: relative;
    width: 1200px;
    height: 756px;
    background: var(--paper);
    overflow: hidden;
  }
  .ornament {
    position: absolute;
    left: 200px;
    top: 146px;
    width: 826px;
    height: 188px;
    border-radius: 50% 50% 8px 8px / 100% 100% 8px 8px;
    background: radial-gradient(ellipse at 50% 70%, rgba(19,40,90,0.55) 0%, rgba(19,40,90,0.28) 55%, rgba(19,40,90,0) 100%);
  }
  .divider {
    position: absolute;
    left: 144px;
    top: 330px;
    width: 940px;
    height: 20px;
  }
  .opening {
    position: absolute;
    top: 420px;
    left: 0;
    width: 1200px;
    text-align: center;
    color: var(--ink);
  }
  .opening__initial {
    font-family: "Pinyon Script", cursive;
    font-size: 84px;
    line-height: 1;
    vertical-align: -6px;
  }
  .opening__rest {
    font-family: "Cormorant Garamond", serif;
    font-style: italic;
    font-weight: 500;
    font-size: 29px;
  }
  .option {
    position: absolute;
    left: 0;
    width: 1200px;
    text-align: center;
    white-space: nowrap;
  }
  .option--one { top: 574px; }
  .option--two { top: 643px; }
  .option--three { top: 700px; }
  .option__label {
    font-family: "Cabin", sans-serif;
    font-weight: 500;
    font-size: 26px;
    color: var(--ink);
  }
  .option--one .option__text {
    font-family: "IM Fell English", serif;
    font-size: 25px;
    color: var(--ink-soft);
  }
  .option--two .option__label,
  .option--two .option__text {
    font-family: "Alice", serif;
    font-weight: 400;
    font-size: 23px;
    color: var(--ink-soft);
  }
  .option--three .option__label,
  .option--three .option__text {
    font-family: "Cabin", sans-serif;
    font-weight: 400;
    font-size: 25px;
    color: var(--ink);
  }
</style>
</head>
<body>
  <main class="page">
    <div class="ornament" role="img" aria-label="Navy scrolling filigree ornament with a central lotus flourish"></div>

    <svg class="divider" viewBox="0 0 940 20" aria-hidden="true">
      <line x1="0" y1="10" x2="940" y2="10" stroke="var(--rule)" stroke-width="3"/>
      <polygon points="469,1 480,10 469,19 458,10" fill="var(--rule)"/>
    </svg>

    <p class="opening">
      <span class="opening__initial">F</span><span class="opening__rest">or over fifteen years,</span>
    </p>

    <p class="option option--one">
      <span class="option__label">Opt1:</span>
      <span class="option__text">Our master craftsmen and builders have been providing high</span>
    </p>

    <p class="option option--two">
      <span class="option__label">Opt2:</span>
      <span class="option__text">&nbsp;quality doors throughout the Southwestern United States and Mexico.</span>
    </p>

    <p class="option option--three">
      <span class="option__label">Opt 3:</span>
      <span class="option__text">Our team of designers loves what they do. That’s what separates Harlow</span>
    </p>
  </main>
</body>
</html>
```